Brightmill Data Works

Our company is about IT hardwares and IT solutions. IT hardware such as PC, RAMS, storage and servers. IT solutions such as project management, BA. We are also selling new technology too.

Target Market(s)

Consumer, Small to Medium Business, Corporate

Requirements
Must have
• The business card must have the following:
• Name:
• Title:
• Contact Number:
• Email address:
• Website:
• Color: Must match the logo color upgrade

```html
<!DOCTYPE html>
<html lang="en">
<head>
<meta charset="utf-8">
<title>Brightmill Data Works – Business Card</title>
<link rel="stylesheet" href="https://fonts.googleapis.com/css2?family=Lato:wght@400;700;900&display=swap">
<style>
  :root {
    --backdrop: #1e1e1f;
    --card-black: #141414;
    --card-white: #fbfbfb;
    --orange-light: #d98a3f;
    --orange-deep: #c8652a;
    --ink: #161616;
    --ink-soft: #4a4a4a;
    --paper-text: #ffffff;
  }
  * { box-sizing: border-box; margin: 0; padding: 0; }
  html, body { width: 1200px; height: 900px; overflow: hidden; }
  body {
    background: var(--backdrop);
    font-family: "Lato", sans-serif;
    position: relative;
  }
  .card {
    position: absolute;
    left: 320px;
    width: 560px;
    height: 320px;
    border-radius: 18px;
    overflow: hidden;
    box-shadow: 0 14px 30px rgba(0,0,0,.5);
  }
  .card--front { top: 95px; background: var(--card-black); display: flex; align-items: center; justify-content: center; }
  .card--back { top: 485px; display: flex; background: var(--ink); }

  .brand { display: flex; align-items: center; gap: 14px; }
  .brand__dot { width: 22px; height: 22px; border-radius: 50%; background: var(--orange-light); flex: none; }
  .brand__name {
    font-weight: 900;
    text-transform: uppercase;
    letter-spacing: 1px;
    line-height: 1.05;
  }
  .card--front .brand { gap: 18px; }
  .card--front .brand__dot { width: 26px; height: 26px; }
  .card--front .brand__name { color: var(--paper-text); font-size: 36px; max-width: 250px; }

  .back__logo-side {
    width: 274px;
    flex: none;
    background: var(--card-white);
    display: flex; align-items: center; justify-content: center;
    padding: 0 24px;
  }
  .back__logo-side .brand { gap: 10px; }
  .back__logo-side .brand__dot { width: 16px; height: 16px; }
  .back__logo-side .brand__name { color: var(--ink-soft); font-size: 22px; max-width: 160px; }

  .back__info-side {
    margin-left: 6px;
    flex: 1;
    background: linear-gradient(135deg, var(--orange-light), var(--orange-deep));
    padding: 86px 0 0 34px;
    color: var(--paper-text);
  }
  .person__name { font-weight: 900; font-size: 20px; color: var(--ink); text-transform: uppercase; letter-spacing: .5px; }
  .person__title { font-size: 13px; margin-top: 2px; }
  .contact { list-style: none; margin-top: 22px; }
  .contact__item { display: flex; align-items: center; gap: 10px; font-size: 14px; margin-bottom: 8px; }
  .contact__item svg { width: 14px; height: 14px; flex: none; }
  .contact__item--web { font-weight: 700; color: var(--ink); padding-left: 24px; }
</style>
</head>
<body>
  <section class="card card--front" aria-label="Business card front">
    <div class="brand">
      <span class="brand__dot"></span>
      <span class="brand__name">Brightmill Data Works</span>
    </div>
  </section>

  <section class="card card--back" aria-label="Business card back">
    <div class="back__logo-side">
      <div class="brand">
        <span class="brand__dot"></span>
        <span class="brand__name">Brightmill Data Works</span>
      </div>
    </div>
    <div class="back__info-side">
      <p class="person__name">Evan Marlow</p>
      <p class="person__title">Managing Director</p>
      <ul class="contact">
        <li class="contact__item">
          <svg viewBox="0 0 16 16" aria-hidden="true"><path fill="#fff" d="M3 2h3l1.5 3.5-2 1.2a9 9 0 0 0 3.8 3.8l1.2-2L14 10v3a1 1 0 0 1-1 1A11 11 0 0 1 2 3a1 1 0 0 1 1-1z"/></svg>
          01632 960418
        </li>
        <li class="contact__item">
          <svg viewBox="0 0 16 16" aria-hidden="true"><rect x="1.5" y="3.5" width="13" height="9" fill="none" stroke="#fff" stroke-width="1.4"/><path d="M1.5 3.5 8 9l6.5-5.5" fill="none" stroke="#fff" stroke-width="1.4"/></svg>
          hello@brightmilldata.co.uk
        </li>
        <li class="contact__item contact__item--web">www.brightmilldata.co.uk</li>
      </ul>
    </div>
  </section>
</body>
</html>
```